Business card por a urban DJ, up scale audience target

Need a sober design, modern, conservative colors but i can consider some options, y play rnb, hip hop, EDM and top40.

Business card for contact and personal info, double sided, use logo attrached please; im 42 so i need a card acording to my age an target audience.

Target Market(s)

Adult people, up scale audience

Industry/Entity Type

Music Download

Contact Information for Business Card

Cel (318) 4207265518 www.lumadrift.com

Requirements
Must have
• open mind
Nice to have
• open mind
Should not have
• DJ

```html
<!DOCTYPE html>
<html lang="en">
<head>
<meta charset="utf-8">
<title>Lumadrift Business Card</title>
<link href="https://fonts.googleapis.com/css2?family=Ubuntu:wght@400;500;700&family=Arimo:wght@400&display=swap" rel="stylesheet">
<style>
  :root {
    --backdrop: #d9d9d9;
    --paper: #ffffff;
    --ink-black: #000000;
    --ink-charcoal: #2b2a2a;
    --ink-stripe: #3a3a3a;
    --text-light: #ffffff;
  }
  html, body {
    margin: 0;
    padding: 0;
    width: 1189px;
    height: 1200px;
    overflow: hidden;
    background: var(--backdrop);
  }
  .sheet {
    position: relative;
    width: 1189px;
    height: 1200px;
  }
  .card {
    position: absolute;
    left: 136px;
    width: 918px;
    height: 523px;
    background: var(--paper);
    box-shadow: 0 4px 10px rgba(0,0,0,0.35);
    overflow: hidden;
  }
  .card--front { top: 46px; }
  .card--back { top: 623px; }

  .card__panels {
    position: absolute;
    inset: 0;
    width: 918px;
    height: 523px;
  }

  .brand {
    position: absolute;
    display: flex;
    align-items: center;
    font-family: "Ubuntu", sans-serif;
    font-weight: 700;
    color: var(--ink-charcoal);
    white-space: nowrap;
  }
  .brand__mark {
    background: var(--ink-charcoal);
    flex: none;
  }
  .card--front .brand {
    left: 40px;
    top: 206px;
    font-size: 40px;
    letter-spacing: 1px;
    gap: 12px;
  }
  .card--front .brand__mark { width: 36px; height: 36px; }
  .card--back .brand {
    left: 0;
    right: 0;
    top: 218px;
    justify-content: center;
    font-size: 64px;
    letter-spacing: 2px;
    gap: 20px;
  }
  .card--back .brand__mark { width: 58px; height: 58px; }

  .identity {
    position: absolute;
    right: 36px;
    top: 82px;
    text-align: right;
    color: var(--text-light);
    font-family: "Ubuntu", sans-serif;
  }
  .identity__name {
    margin: 0;
    font-size: 43px;
    font-weight: 500;
    line-height: 1;
  }
  .identity__role {
    margin: 10px 0 0;
    font-size: 30px;
    font-weight: 400;
    line-height: 1;
  }

  .contacts {
    position: absolute;
    right: 36px;
    top: 318px;
    margin: 0;
    padding: 0;
    list-style: none;
    font-family: "Arimo", sans-serif;
    font-size: 24.5px;
    color: var(--text-light);
  }
  .contacts__item {
    display: flex;
    justify-content: flex-end;
    align-items: center;
    gap: 20px;
    height: 40px;
  }
  .contacts__icon {
    width: 20px;
    height: 20px;
    flex: none;
  }
</style>
</head>
<body>
<main class="sheet">

  <section class="card card--front" aria-label="Card front">
    <svg class="card__panels" viewBox="0 0 918 523" aria-hidden="true">
      <polygon points="306,0 918,0 918,523 313,523 506,260" fill="var(--ink-stripe)"/>
      <polygon points="292,0 918,0 918,523 300,523 492,260" fill="var(--ink-charcoal)"/>
      <polygon points="312,0 918,0 918,260 512,260" fill="var(--ink-black)"/>
      <polygon points="292,0 306,0 506,260 492,260" fill="var(--ink-stripe)"/>
    </svg>

    <div class="brand"><span class="brand__mark"></span>LUMADRIFT</div>

    <div class="identity">
      <h1 class="identity__name">Dane Corwell</h1>
      <p class="identity__role">Managing Director</p>
    </div>

    <ul class="contacts">
      <li class="contacts__item">(318) 4207265518
        <svg class="contacts__icon" viewBox="0 0 20 20" aria-hidden="true"><rect width="20" height="20" fill="#fff"/><path d="M4 8c0-2 3-3 6-3s6 1 6 3v1h-3V8H7v1H4z M6 10h8l1 5H5z" fill="var(--ink-charcoal)"/></svg>
      </li>
      <li class="contacts__item">info@lumadrift.com
        <svg class="contacts__icon" viewBox="0 0 20 20" aria-hidden="true"><rect width="20" height="20" fill="#fff"/><rect x="3" y="5" width="14" height="10" fill="var(--ink-charcoal)"/><path d="M3 5l7 6 7-6" stroke="#fff" stroke-width="1.3" fill="none"/></svg>
      </li>
      <li class="contacts__item">www.lumadrift.com
        <svg class="contacts__icon" viewBox="0 0 20 20" aria-hidden="true"><rect width="20" height="20" fill="#fff"/><circle cx="10" cy="10" r="6.5" fill="var(--ink-charcoal)"/><path d="M6 7c2 0 3 2 2 4s2 3 3 1 3-2 3-4" stroke="#fff" stroke-width="1.2" fill="none"/></svg>
      </li>
      <li class="contacts__item">418 Harlow St, Camden NJ 081
        <svg class="contacts__icon" viewBox="0 0 20 20" aria-hidden="true"><rect width="20" height="20" fill="#fff"/><path d="M10 3a4.5 4.5 0 0 1 4.5 4.5C14.5 11 10 16 10 16S5.5 11 5.5 7.5A4.5 4.5 0 0 1 10 3z" fill="var(--ink-charcoal)"/><circle cx="10" cy="7.5" r="1.6" fill="#fff"/></svg>
      </li>
    </ul>
  </section>

  <section class="card card--back" aria-label="Card back">
    <div class="brand"><span class="brand__mark"></span>LUMADRIFT</div>
  </section>

</main>
</body>
</html>
```